Elegant and modern Wedding Photography brochure

My existing brochure (attached) needs a major facelift. This is one of the main selling tools - it gets emailed to my clients when they make an equiry on what packages i offer and it is printed out and walked through at our first meeting. This brochure is as critical as my website - it needs to sing!

I'm looking for an eye-catching design that says:
Elegant
Modern
Clean
Crisp
Not cutesy or lovey-dovey thanks - we are more sophisticated and professional than that.

Update images to some of the latest weddings I've shot also. Let me know files and resolution you need. I've enabled right-click to download images on my site for a limited time. Please note that I retain copyright and will pursue any breeches.

Http://www.sarahkelbrin.com/Melbourne-wedding-photography
Updates

Thanks for all of your designs! Will take a few days to decide.

Target Market(s)

Australian Women aged 24-44

Industry/Entity Type

Wedding

Font styles to use
Other font styles liked:
• Century Gothic

Requirements
Must have
• Easy to print - does not have to be 6 A4 pages like the existing brochure
Nice to have
• Some full page images - The photos are supposed to be the hero here :-)
Should not have
• Not cutesy or lovey-dovey thanks - we are more sophisticated and professional than that.

No black backgrounds, I prefer a white thanks

No images in organic shaped boxes (like the rectangles in the logo - no thanks).
Keep the lines straight and sharp

```html
<!DOCTYPE html>
<html lang="en">
<head>
<meta charset="utf-8">
<title>Sarah's approach – Wedding Photography</title>
<link href="https://fonts.googleapis.com/css2?family=Didact+Gothic&family=Jost:wght@500;600&display=swap" rel="stylesheet">
<style>
  :root {
    --plum: #8a2c8e;
    --ink: #1f1f1f;
    --paper: #ffffff;
    --photo-green: #8fa46a;
    --photo-dark: #3d4a2f;
    --photo-warm: #d9cfa8;
    --photo-path: #b9b2a3;
  }
  * { box-sizing: border-box; margin: 0; padding: 0; }
  html, body { width: 1200px; height: 856px; overflow: hidden; background: var(--paper); }
  .page {
    position: relative; width: 1200px; height: 856px;
    font-family: "Didact Gothic", "Century Gothic", sans-serif;
    color: var(--ink);
  }
  .page-title {
    position: absolute; left: 58px; top: 52px;
    font-family: "Jost", "Century Gothic", sans-serif; font-weight: 600;
    font-size: 43px; line-height: 1; color: var(--plum); letter-spacing: 0.2px;
  }
  .page-subtitle {
    position: absolute; left: 58px; top: 95px;
    font-size: 19px; line-height: 1.1;
  }
  .photo { position: absolute; }
  .photo-hero {
    left: 58px; top: 150px; width: 502px; height: 334px;
    background: radial-gradient(ellipse at 60% 55%, #e8d8c4 0%, #c9c7a0 35%, var(--photo-green) 70%, #6d7f4e 100%);
  }
  .photo-couple { left: 905px; top: 140px; width: 238px; height: 158px;
    background: linear-gradient(90deg, #4a3d33 0%, var(--photo-green) 35%, #f2f0ec 55%, #2c2c34 80%, #4d5a3a 100%); }
  .photo-flowergirls { left: 905px; top: 308px; width: 238px; height: 158px;
    background: linear-gradient(180deg, #3f5a2a 0%, #5f7a3c 45%, var(--photo-path) 75%, #a39a88 100%); }
  .photo-party { left: 905px; top: 473px; width: 238px; height: 158px;
    background: linear-gradient(180deg, #7e9a50 0%, #4f6435 50%, #6b7f45 100%); }
  .photo-bridesmaids { left: 905px; top: 640px; width: 238px; height: 158px;
    background: linear-gradient(180deg, #c7d98a 0%, #8fae55 40%, #444a55 65%, #6e9a3e 100%); }

  .text-block { position: absolute; font-size: 15.6px; line-height: 18.6px; }
  .text-block h2 {
    font-family: "Jost", "Century Gothic", sans-serif; font-weight: 600;
    font-size: 17px; line-height: 20px; color: var(--plum);
  }
  .text-block p + p { margin-top: 18.6px; }
  .style-approach { left: 58px; top: 497px; width: 236px; }
  .style-approach h2 { margin-bottom: 20px; }
  .formal-photography { left: 304px; top: 497px; width: 252px; }
  .right-column { left: 658px; top: 138px; width: 232px; }
  .right-column h2 { margin: 20px 0 20px; }

  .contact-line {
    position: absolute; left: 58px; top: 790px;
    font-size: 13.4px; color: var(--plum);
    display: flex; align-items: center; gap: 8px;
  }
  .contact-sep { width: 5px; height: 5px; border-radius: 50%; background: var(--plum); }
  .footer-rule { position: absolute; left: 58px; top: 817px; width: 1073px; height: 4px; background: var(--plum); }
</style>
</head>
<body>
<main class="page">
  <h1 class="page-title">Sarah’s approach…</h1>
  <p class="page-subtitle">Enjoy your special day</p>

  <div class="photo photo-hero" role="img" aria-label="Bride and groom embracing among white garden flowers"></div>

  <section class="text-block style-approach">
    <h2>Style &amp; Approach</h2>
    <p>Sarah can observe and capture your wedding day in the background, quickly and quietly taking photojournalistic pictures rather than directing it if you prefer. Or she can confidently play the role of Art Director and instruct beautiful poses. Either way, what is most important is that her clients are relaxed and having a really great time on their wedding day!</p>
  </section>

  <section class="text-block formal-photography">
    <h2>Formal Photography</h2>
    <p>Many of Sarah’s clients book her because of the easy-going approach she has. They can get on with having a great time on their day without worrying about formal photography. However, there are occasions when clients do want formal family pictures, and Sarah is more than happy to accommodate their requests.</p>
    <p>In order to keep the disruption on the day to a minimum, we recommend that Sarah</p>
  </section>

  <section class="text-block right-column">
    <p>photographs no more than 6 groups, and a select number of the special couple.</p>
    <h2>Image Presentation</h2>
    <p>The most professional way of presenting clients with their photographs is in an elegantly designed photo book. Sarah’s clients only pay one fixed price for the photography, regardless of how many images taken. There are no hard sell procedures to go through, and the completed book is prepared within 2-6 weeks after the wedding day.</p>
    <h2>Time of Year</h2>
    <p>Signature pictures can be taken on overcast days or winter months. Don’t worry if the sky is not perfectly blue. In the end, regardless of the weather – it’s the timeless mood of the day that Sarah strives to capture.</p>
  </section>

  <div class="photo photo-couple" role="img" aria-label="Bride and groom posing between trees"></div>
  <div class="photo photo-flowergirls" role="img" aria-label="Two flower girls walking along a garden path"></div>
  <div class="photo photo-party" role="img" aria-label="Bridal party celebrating under park trees"></div>
  <div class="photo photo-bridesmaids" role="img" aria-label="Bridesmaids in grey gowns on a sunny lawn"></div>

  <footer>
    <p class="contact-line">
      <span>www.sarahkelbrin.com</span><span class="contact-sep"></span>
      <span>Mobile: 0491 570 156 2</span><span class="contact-sep"></span>
      <span>Email: sarah@sarahkelbrin.com</span>
    </p>
    <div class="footer-rule"></div>
  </footer>
</main>
</body>
</html>
```